Design 12 simple icons for a Fintech website

We are Merrow Capital Systems, a successful fintech startup that will be launching a new product within the next few months.

Our Software as a Service product has 12 distinct Features, and we need 12 simple customised graphics to visually portray these features on our website.

Each of these Features falls under one of these categories: Information Management, Valuation and Analysis, and Process Visualisation. Each category has a different colour of glyphicons, as you can see here on our website: http://www.merrowcs.example/features/

Currently we are using coloured glyphicons from Pictolane as our graphics for these Features (see here: http://www.pictolane.example/packs/prime-symbolsets). However, these graphics are not expressing each of our paragraph descriptions as clearly as we would like.

We have 3 requirements for this project:
1. The brand message
2. Colour palette
3. Design style
These requirements are further explained below.

We also have a list of "buzzwords" to guide you to design each of the 12 Feature graphics which we will attach here. These buzzwords, along with the paragraph descriptions beside each Feature on the website, should assist you in understanding and designing these Feature graphics.

Target Market(s)

Asset managers and funds managers

Industry/Entity Type

Finance

Requirements
Must have
• 1. Brand message of graphics:
• We as a brand want to communicate the ideas of "innovation, professional, financial institution, trustworthy, liberation, data/analytics, and insight" throughout our brand.
• 2. Colour palette:
• - Our colour palette is based on Vanta Surface Guide colours
• - We would like each of the 3 categories of Features to be distinct, i.e. use 3 different colours for the 3 different categories.
• - We have chosen these 3 colours: teal #009688, light blue #03A9F4, indigo #3F51B5
• 3. Design style:
• We would like the graphics to be modern, flat, and following the Vanta Surface Guide outline (http://www.vantasurface.example/guide/spec/style/color.html#color-color-palette) , i.e. the design should be flat.
• 4. File format
• We would like the files to be in Adobe Illustrator (.ai) format
Should not have
• - 3D design, i.e. the graphics should not appear like they have shadows

```html
<!DOCTYPE html>
<html lang="en">
<head>
<meta charset="utf-8">
<title>Broker Deep Estimates and Ad Hoc Analysis</title>
<link rel="stylesheet" href="https://fonts.googleapis.com/css2?family=Josefin+Sans:wght@400&display=swap">
<style>
  :root {
    --accent: #03a9f4;
    --divider: #30508a;
    --placeholder: #dff3fd;
    --paper: #ffffff;
  }
  html, body {
    margin: 0;
    padding: 0;
    width: 1200px;
    height: 1000px;
    overflow: hidden;
    background: var(--paper);
  }
  .canvas {
    position: relative;
    width: 1200px;
    height: 1000px;
  }
  .diagram {
    position: absolute;
    inset: 0;
  }
  .stroke {
    fill: none;
    stroke: var(--accent);
    stroke-width: 4;
    stroke-linecap: round;
    stroke-linejoin: round;
  }
  .stroke-thin { stroke-width: 2; }
  .solid { fill: var(--accent); }
  .divider-line {
    stroke: var(--divider);
    stroke-width: 4;
    stroke-linecap: round;
  }
  .person-slot { fill: var(--placeholder); }
  .feature-title {
    position: absolute;
    margin: 0;
    font-family: "Josefin Sans", sans-serif;
    font-weight: 400;
    color: var(--accent);
    font-size: 34px;
    line-height: 1;
    letter-spacing: 1.5px;
    white-space: nowrap;
  }
  .feature-title--broker { left: 583px; top: 224px; }
  .feature-title--adhoc { left: 653px; top: 735px; }
</style>
</head>
<body>
<main class="canvas">
  <svg class="diagram" width="1200" height="1000" viewBox="0 0 1200 1000" xmlns="http://www.w3.org/2000/svg">
    <!-- Broker deep estimates: input icons -->
    <g class="input-icons">
      <circle class="stroke" cx="135" cy="127" r="43"/>
      <rect class="solid" x="109" y="121" width="15" height="25" rx="7"/>
      <rect class="solid" x="128" y="111" width="15" height="35" rx="7"/>
      <rect class="solid" x="147" y="101" width="15" height="45" rx="7"/>

      <circle class="stroke" cx="135" cy="266" r="43"/>
      <polyline class="stroke stroke-thin" points="111,281 124,263 136,281 148,259 162,273" stroke-dasharray="2 3"/>
      <circle class="solid" cx="111" cy="281" r="4"/>
      <circle class="solid" cx="124" cy="263" r="4"/>
      <circle class="solid" cx="136" cy="281" r="4"/>
      <circle class="solid" cx="148" cy="259" r="4"/>
      <circle class="solid" cx="162" cy="273" r="4"/>

      <circle class="stroke" cx="135" cy="399" r="43"/>
      <path class="stroke stroke-thin" d="M143 383 H119 V420 H152 V398"/>
      <path class="stroke stroke-thin" d="M136 406 L155 387 L158 390 L139 409 L134 411 Z"/>
    </g>
    <g class="connectors">
      <polyline class="stroke" points="178,128 275,128 275,178"/>
      <line class="stroke" x1="178" y1="266" x2="231" y2="266"/>
      <polyline class="stroke" points="178,402 275,402 275,325"/>
    </g>
    <rect class="person-slot" x="246" y="172" width="58" height="160" rx="8" role="img" aria-label="Outline figure of a broker"/>
    <g class="exchange-arrow">
      <line class="stroke stroke-thin" x1="297" y1="223" x2="345" y2="223"/>
      <polyline class="stroke stroke-thin" points="306,213 297,223 306,232"/>
      <polyline class="stroke stroke-thin" points="336,213 345,223 336,232"/>
    </g>
    <rect class="person-slot" x="399" y="172" width="58" height="160" rx="8" role="img" aria-label="Outline figure of a client"/>

    <line class="divider-line" x1="97" y1="499" x2="1105" y2="499"/>

    <!-- Ad hoc analysis: source icons -->
    <g class="source-icons">
      <circle class="stroke stroke-thin" cx="157" cy="611" r="36"/>
      <rect class="stroke stroke-thin" x="144" y="596" width="26" height="30" rx="2"/>

      <circle class="stroke stroke-thin" cx="274" cy="611" r="36"/>
      <path class="stroke stroke-thin" d="M264 623 H261 V593 H280 V596"/>
      <path class="stroke stroke-thin" d="M271 628 H267 V598 H286 V601"/>
      <rect class="stroke stroke-thin" x="273" y="603" width="21" height="31"/>

      <circle class="stroke stroke-thin" cx="390" cy="611" r="36"/>
      <rect class="solid" x="372" y="609" width="10" height="16" rx="5"/>
      <rect class="solid" x="385" y="601" width="10" height="24" rx="5"/>
      <rect class="solid" x="398" y="595" width="10" height="30" rx="5"/>
    </g>
    <g class="connectors">
      <line class="stroke stroke-thin" x1="157" y1="647" x2="157" y2="715"/>
      <line class="stroke stroke-thin" x1="274" y1="647" x2="274" y2="715"/>
      <line class="stroke stroke-thin" x1="390" y1="647" x2="390" y2="715"/>
      <line class="stroke stroke-thin" x1="155" y1="759" x2="392" y2="759"/>
    </g>
    <rect class="person-slot" x="160" y="755" width="78" height="197" rx="10" role="img" aria-label="Outline figure of an analyst in a tie"/>
    <rect class="person-slot" x="316" y="755" width="78" height="197" rx="10" role="img" aria-label="Outline figure of a second analyst in a tie"/>
  </svg>

  <h2 class="feature-title feature-title--broker">BROKER DEEP ESTIMATES</h2>
  <h2 class="feature-title feature-title--adhoc">AD HOC ANALYSIS</h2>
</main>
</body>
</html>
```